Website Redesign Project Puzzle Vault Larkfield

We are an escape room company located in Ashburn, Virginia. We currently have a website https://www.puzzlevaultlarkfield.example based upon html/bootstrap/javascript/php/mysql and I'd like to keep it that way. I'm looking for someone upgrade the front page so it is more informative, cleaner, quicker to load, and optimizes the space for full sale opportunities.

Target Market(s)

Corporate Clients, Families, Friends. All ages

Industry/Entity Type

Entertainment Industry

Coding

Coded - Design and coding required

Number of Pages Required

3 page

Font styles to use
Other font styles liked:
• Similar to Facebook or Amazon

Requirements
Must have
• Must be mobile friendly. bootstrap. Lots of graphics (will provide) nice and easy to read fonts. Easy to read layout. Must look clean, fresh, exciting, and want to grab attention.
• Please visit my facebook page and website for more details. facebook.com/puzzlevaultlarkfield
Nice to have
• Same color as existing but open to options if they look nice.
Should not have
• Should not be wordpress or hard to modify.

```html
<!DOCTYPE html>
<html lang="en">
<head>
<meta charset="utf-8">
<title>Puzzle Vault Larkfield</title>
<link rel="stylesheet" href="https://fonts.googleapis.com/css2?family=Khand:wght@400;500;600&family=Quicksand:wght@400;500;700&family=Oswald:wght@400;500&display=swap">
<style>
:root{
  --ink:#0f1215;
  --dark:#15181d;
  --blue:#1f9cea;
  --blue-bright:#2aa9f4;
  --blue-deep:#1583d6;
  --navy:#1a2a72;
  --navy-deep:#101c52;
  --white:#ffffff;
  --muted:#c9d6e6;
}
*{box-sizing:border-box;margin:0;padding:0}
html,body{width:1200px;height:4688px;overflow:hidden}
body{position:relative;background:var(--ink);font-family:"Quicksand",sans-serif;color:var(--white)}
.abs{position:absolute}
.head{font-family:"Khand",sans-serif;font-weight:500}
.caps{font-family:"Oswald",sans-serif;text-transform:uppercase}

/* header */
.site-header{left:0;top:0;width:1200px;height:137px;background:var(--ink)}
.brand{display:flex;align-items:center;gap:12px}
.brand-square{width:44px;height:44px;border:3px solid var(--blue)}
.brand-name{font-family:"Khand",sans-serif;font-weight:600;color:var(--blue);font-size:30px;line-height:1;text-transform:uppercase}
.site-header .brand{left:96px;top:30px}
.phone{left:752px;top:28px;font-family:"Khand",sans-serif;font-size:24px;display:flex;align-items:center;gap:12px}
.btn-book{left:972px;top:24px;width:136px;height:40px;background:var(--blue);font-family:"Khand",sans-serif;font-size:18px;display:flex;align-items:center;justify-content:center}
.main-nav{left:416px;top:92px;display:flex;gap:46px;font-family:"Khand",sans-serif;font-size:16px;text-transform:uppercase}

/* hero */
.hero{left:0;top:137px;width:1200px;height:610px;background:linear-gradient(90deg,#0f1320 0%,#1a2236 45%,#26354f 100%)}
.hero-photo{left:540px;top:0;width:660px;height:610px;background:linear-gradient(160deg,#25385a,#3a4e6e 50%,#1b2336)}
.hero .brand{left:90px;top:175px}
.hero .brand-square{width:110px;height:180px;border:4px solid var(--blue)}
.hero-title{font-family:"Khand",sans-serif;font-weight:600;font-size:110px;line-height:.88;text-transform:uppercase}
.hero-sub{font-family:"Khand",sans-serif;font-size:42px;letter-spacing:8px;text-align:right;text-transform:uppercase}
.dots{left:88px;top:525px;display:flex;gap:10px}
.dots span{width:18px;height:18px;border-radius:50%;border:2px solid #fff}
.dots span.on{background:#fff}

/* rooms */
.room-shot{top:747px;width:300px;height:191px;background:linear-gradient(135deg,#2d3850,#5b3a2b)}
.difficulty{top:747px;width:44px;height:191px;display:flex;align-items:center;justify-content:center}
.difficulty span{transform:rotate(-90deg);white-space:nowrap;font-family:"Khand",sans-serif;font-size:20px}
.room{top:938px;width:300px;height:300px;padding:22px 40px 0 66px}
.room.blue{background:var(--blue)}
.room.dark{background:var(--ink)}
.room h3{font-family:"Khand",sans-serif;font-weight:500;font-size:24px;text-transform:uppercase;margin:18px 0 14px}
.room p{font-size:13.5px;line-height:1.7}
.room svg{display:block}

/* corporate */
.corp-photo{left:0;top:1238px;width:1200px;height:583px;background:linear-gradient(180deg,#2c3b5a,#506177 60%,#39465a)}
.corp-title{left:0;top:1490px;width:1200px;text-align:center;font-family:"Khand",sans-serif;font-weight:600;font-size:104px;letter-spacing:2px;text-transform:uppercase}
.blue-band{left:0;top:1821px;width:1200px;height:546px;background:linear-gradient(180deg,var(--blue-bright),var(--blue-deep))}
.event-card{top:1712px;width:318px;height:218px;background:#fff;color:var(--ink);text-align:center;padding-top:38px;box-shadow:0 4px 14px rgba(0,0,0,.25)}
.event-card h4{font-family:"Khand",sans-serif;font-weight:500;font-size:25px;line-height:1.1}
.event-card .meta{font-family:"Khand",sans-serif;font-size:23px;color:var(--blue)}
.btn-outline{display:inline-block;margin-top:16px;padding:6px 22px;border:2px solid var(--blue);color:var(--blue);font-family:"Khand",sans-serif;font-size:16px;text-transform:uppercase}

/* forms */
.section-title{left:0;width:1200px;text-align:center;font-family:"Khand",sans-serif;font-weight:500;font-size:50px}
.field{height:46px;border:1px solid rgba(255,255,255,.75);font-size:15px;padding:12px 16px}
.field.tall{height:74px}
.btn-send{width:206px;height:46px;border-radius:23px;background:var(--ink);font-family:"Oswald",sans-serif;font-size:15px;display:flex;align-items:center;justify-content:center;text-transform:uppercase}
.caret{position:absolute;right:14px;top:20px;border:5px solid transparent;border-top-color:#fff}

/* birthday */
.bday{left:0;top:2367px;width:1200px;height:638px;background:var(--dark);clip-path:polygon(0 0,660px 62px,1200px 10px,1200px 610px,660px 560px,0 638px)}
.bday-photo{left:0;top:2367px;width:710px;height:638px;background:linear-gradient(135deg,#5b6a82,#8c7b6a 50%,#3d4c3a);clip-path:polygon(0 0,660px 62px,710px 58px,710px 556px,660px 560px,0 638px)}
.bday h2{left:723px;top:2465px;font-family:"Khand",sans-serif;font-weight:500;font-size:48px}
.bday-copy{left:725px;top:2538px;width:384px;font-size:15px;line-height:1.9;text-align:justify}
.price{top:2732px;width:168px;height:141px;background:var(--blue);text-align:center;padding-top:26px;font-family:"Khand",sans-serif;font-size:17px;line-height:1.2}
.price strong{display:block;font-size:32px;font-weight:500}
.fine{left:728px;top:2888px;font-family:"Khand",sans-serif;font-style:normal;font-size:13px;color:#dfe7f1}

/* faq */
.faq{left:0;top:3533px;width:1200px;height:710px;background:linear-gradient(180deg,var(--navy),var(--navy-deep))}
.faq-intro{left:180px;top:3680px;width:840px;text-align:center;font-size:14px;line-height:1.75}
.faq-item{width:492px;height:90px;border:1.5px solid rgba(255,255,255,.8);border-radius:4px;padding:18px 22px}
.faq-item h5{font-family:"Khand",sans-serif;font-weight:500;font-size:19px}
.faq-item p{font-size:15px;line-height:1.2}
.faq-item u{font-weight:700}
.btn-pill{left:509px;top:4064px;width:182px;height:48px;border-radius:24px;background:var(--blue);font-family:"Oswald",sans-serif;font-size:17px;display:flex;align-items:center;justify-content:center;text-transform:uppercase}

/* footer */
.footer{left:0;top:4243px;width:1200px;height:391px;background:linear-gradient(180deg,var(--blue-bright),var(--blue))}
.footer-nav{left:0;top:4382px;width:1200px;display:flex;justify-content:center;gap:70px;font-family:"Khand",sans-serif;font-size:17px;text-transform:uppercase}
.contact-col{top:4433px;width:320px;text-align:center;font-family:"Khand",sans-serif;font-size:16px;line-height:1.3}
.icon-disc{width:58px;height:58px;border-radius:50%;background:#fff;margin:0 auto 20px;display:flex;align-items:center;justify-content:center}
.hours{left:0;top:4588px;width:1200px;text-align:center;font-family:"Khand",sans-serif;font-size:13px}
.bottom-bar{left:0;top:4634px;width:1200px;height:54px;background:var(--ink);font-size:13px}
.social{display:flex;gap:14px}
.social span{width:18px;height:18px;border-radius:50%;background:#fff}
</style>
</head>
<body>

<header class="abs site-header">
  <div class="abs brand"><span class="brand-square"></span><span class="brand-name">Puzzle Vault<br>Larkfield</span></div>
  <div class="abs phone">
    <svg width="18" height="18" viewBox="0 0 24 24"><path d="M6.6 10.8a15 15 0 0 0 6.6 6.6l2.2-2.2a1 1 0 0 1 1-.25 11.4 11.4 0 0 0 3.6.6 1 1 0 0 1 1 1V20a1 1 0 0 1-1 1A17 17 0 0 1 3 4a1 1 0 0 1 1-1h3.5a1 1 0 0 1 1 1c0 1.25.2 2.45.6 3.6a1 1 0 0 1-.25 1z" fill="#fff"/></svg>
    (555) 014 2290
  </div>
  <div class="abs btn-book">BOOK NOW</div>
  <nav class="abs main-nav"><span>Escape Rooms</span><span>Special Events</span><span>Locations</span><span>How It Works</span><span>Contact Us</span></nav>
</header>

<section class="abs hero">
  <div class="abs hero-photo" role="img" aria-label="Photo of a group of smiling kids posing in front of the branded wall"></div>
  <div class="abs brand">
    <span class="brand-square"></span>
    <div><div class="hero-title">Puzzle<br>Vault</div><div class="hero-sub">Larkfield</div></div>
  </div>
  <div class="abs dots"><span class="on"></span><span></span><span></span><span></span></div>
</section>

<!-- rooms -->
<div class="abs room-shot" style="left:0" role="img" aria-label="Photo of players in orange jumpsuits"></div>
<div class="abs room-shot" style="left:300px" role="img" aria-label="Photo of a family group in the candy shop room"></div>
<div class="abs room-shot" style="left:600px" role="img" aria-label="Photo of a group celebrating with money props"></div>
<div class="abs room-shot" style="left:900px" role="img" aria-label="Photo of players behind jail bars"></div>
<div class="abs difficulty" style="left:0;background:var(--ink)"><span>DIFFICULTY: 10/10</span></div>
<div class="abs difficulty" style="left:300px;background:var(--blue)"><span>DIFFICULTY: 7/10</span></div>
<div class="abs difficulty" style="left:600px;background:var(--ink)"><span>DIFFICULTY: 8/10</span></div>
<div class="abs difficulty" style="left:900px;background:var(--blue)"><span>DIFFICULTY: 8/10</span></div>

<div class="abs room blue" style="left:0">
  <svg width="48" height="48" viewBox="0 0 48 48"><circle cx="24" cy="24" r="21" fill="none" stroke="#fff" stroke-width="2.5"/><path d="M17 16l4 5h-8zM31 32l-4-5h8z" fill="#fff"/></svg>
  <h3>Elevator</h3>
  <p>The main elevators are down so you'll need to take the freight elevator to the top floor if you want to get your award. The last celebrity that attempted to do so wasn't so lucky.</p>
</div>
<div class="abs room dark" style="left:300px">
  <svg width="48" height="48" viewBox="0 0 48 48"><circle cx="24" cy="24" r="9" fill="none" stroke="#fff" stroke-width="2.5"/><path d="M15 24l-9-6v12zM33 24l9-6v12z" fill="none" stroke="#fff" stroke-width="2.5"/></svg>
  <h3>Candy Shop</h3>
  <p>With all of the candy right before your eyes, find the golden ticket and win the prize!</p>
</div>
<div class="abs room blue" style="left:600px">
  <svg width="48" height="48" viewBox="0 0 48 48"><circle cx="28" cy="8" r="4" fill="none" stroke="#fff" stroke-width="2.5"/><path d="M12 20l10-6 8 6-4 10 8 10M24 30l-8 12" fill="none" stroke="#fff" stroke-width="2.5"/></svg>
  <h3>Bank Heist</h3>
  <p>With your family held hostage, the mob gave you one choice - rob the bank in exchange for their freedom or its goodbyes forever.</p>
</div>
<div class="abs room dark" style="left:900px;padding-left:78px">
  <svg width="30" height="40" viewBox="0 0 30 40"><rect x="2" y="2" width="26" height="36" fill="none" stroke="#fff" stroke-width="2"/><path d="M10 2v36M20 2v36M2 14h26M2 26h26" stroke="#fff" stroke-width="2"/></svg>
  <h3 style="margin-top:10px;margin-bottom:4px">Jail Break</h3>
  <p>One Guard, One Goal: get out.</p>
</div>

<!-- corporate -->
<div class="abs corp-photo" role="img" aria-label="Photo of a large corporate group posing together in the lobby"></div>
<div class="abs corp-title">Corporate Events</div>
<div class="abs blue-band"></div>

<div class="abs event-card" style="left:91px;padding-top:42px">
  <h4>On-site multi-room</h4>
  <div class="meta">Accommodate up to 30 people</div>
  <span class="btn-outline">Buy Now</span>
</div>
<div class="abs event-card" style="left:441px;padding-top:30px">
  <h4>Off-site Hot Seat<br>Escape Room</h4>
  <div class="meta">Number of Players: 20 to 100</div>
  <span class="btn-outline">Buy Now</span>
</div>
<div class="abs event-card" style="left:791px;padding-top:30px">
  <h4>Off-site Custom<br>Escape Room</h4>
  <div class="meta">Number of Players: 30+</div>
  <span class="btn-outline">Buy Now</span>
</div>

<h2 class="abs section-title" style="top:2000px">Contact Us</h2>
<div class="abs field" style="left:88px;top:2085px;width:250px">Name</div>
<div class="abs field" style="left:357px;top:2085px;width:250px">Phone Number</div>
<div class="abs field" style="left:627px;top:2085px;width:232px">Email</div>
<div class="abs field" style="left:878px;top:2085px;width:232px">Select a Package<span class="caret"></span></div>
<div class="abs field tall" style="left:88px;top:2149px;width:1022px">Message</div>
<div class="abs btn-send" style="left:497px;top:2242px">Send Message</div>

<!-- birthday -->
<section class="abs" style="left:0;top:3005px;width:1200px;height:528px;background:linear-gradient(180deg,var(--blue-bright),var(--blue-deep))"></section>
<div class="abs bday"></div>
<div class="abs bday-photo" role="img" aria-label="Photo of a family celebrating a birthday in the candy shop room"></div>
<h2 class="abs bday" style="background:none;clip-path:none;height:auto;width:auto"></h2>
<div class="abs" style="left:723px;top:2465px;font-family:'Khand',sans-serif;font-weight:500;font-size:48px">Birthday Parties</div>
<p class="abs bday-copy">Celebrate this year in style by treating your family with an escape room birthday package. You and your loved ones have the choice of four escape rooms and will enjoy a private party afterwards in our party room. Either of these packages will be sure to satisfy your needs</p>
<div class="abs price" style="left:725px">Add just<strong>$150</strong>to your escape room</div>
<div class="abs price" style="left:905px">Add just<strong>$125</strong>Bring your own food</div>
<div class="abs fine">A $50 cleaning fee applies to all parties who don't clean after themselves</div>

<h2 class="abs section-title" style="top:3088px">Contact Us</h2>
<div class="abs field" style="left:90px;top:3170px;width:330px">Name</div>
<div class="abs field" style="left:435px;top:3170px;width:330px">Phone Number</div>
<div class="abs field" style="left:780px;top:3170px;width:330px">Group Size</div>
<div class="abs field" style="left:90px;top:3234px;width:502px">Which Package<span class="caret"></span></div>
<div class="abs field" style="left:608px;top:3234px;width:502px">Email</div>
<div class="abs field tall" style="left:90px;top:3300px;width:1020px">Message</div>
<div class="abs btn-send" style="left:499px;top:3392px">Send Message</div>

<!-- faq -->
<section class="abs faq"></section>
<h2 class="abs section-title" style="top:3590px">Faq</h2>
<p class="abs faq-intro">An escape room is a themed environment where you and your friends must work together to complete the objectives through solving puzzles before time runs out. Most missions will lock you in while some of our missions do not.</p>
<div class="abs faq-item" style="left:97px;top:3742px"><h5>How do I make a reservation?</h5><p>Click on the Book now button or click here <u>BOOK NOW</u></p></div>
<div class="abs faq-item" style="left:606px;top:3742px"><h5>How long does an escape last?</h5><p>Each escape lasts 60 minutes</p></div>
<div class="abs faq-item" style="left:97px;top:3850px"><h5>I'm pregnant, can I participate?</h5><p>Less than 8 months yes.</p></div>
<div class="abs faq-item" style="left:606px;top:3850px;padding-top:14px"><h5>How can I redeem a voucher or promo code?</h5><p>Click on the Book Now button and enter the code in the promo code text box.</p></div>
<div class="abs faq-item" style="left:97px;top:3958px"><h5>Where do I park?</h5><p>Plenty of parking in front of the building</p></div>
<div class="abs faq-item" style="left:606px;top:3958px"><h5>Which room is the most challenging?</h5><p>They are all challenging!</p></div>
<div class="abs btn-pill">View All</div>

<!-- footer -->
<footer class="abs footer"></footer>
<div class="abs brand" style="left:520px;top:4262px"><span class="brand-square" style="border-color:var(--ink)"></span><span class="brand-name" style="color:#fff">Puzzle Vault<br>Larkfield</span></div>
<nav class="abs footer-nav"><span>Escape Rooms</span><span>Special Events</span><span>Locations</span><span>How It Works</span><span>Contact Us</span></nav>

<div class="abs contact-col" style="left:160px">
  <div class="icon-disc"><svg width="26" height="26" viewBox="0 0 24 24"><path d="M12 2a7 7 0 0 0-7 7c0 5 7 13 7 13s7-8 7-13a7 7 0 0 0-7-7z" fill="none" stroke="var(--blue)" stroke-width="2"/><circle cx="12" cy="9" r="2.5" fill="none" stroke="var(--blue)" stroke-width="2"/></svg></div>
  1180 Meadowgate Drive, Suite 210,<br>Larkfield, VA 20190
</div>
<div class="abs contact-col" style="left:445px">
  <div class="icon-disc"><svg width="26" height="26" viewBox="0 0 24 24"><path d="M6.6 10.8a15 15 0 0 0 6.6 6.6l2.2-2.2a1 1 0 0 1 1-.25 11.4 11.4 0 0 0 3.6.6 1 1 0 0 1 1 1V20a1 1 0 0 1-1 1A17 17 0 0 1 3 4a1 1 0 0 1 1-1h3.5a1 1 0 0 1 1 1c0 1.25.2 2.45.6 3.6a1 1 0 0 1-.25 1z" fill="none" stroke="var(--blue)" stroke-width="1.8"/></svg></div>
  (555) 014 2290
</div>
<div class="abs contact-col" style="left:735px">
  <div class="icon-disc"><svg width="26" height="26" viewBox="0 0 24 24"><rect x="3" y="5" width="18" height="14" fill="none" stroke="var(--blue)" stroke-width="2"/><path d="M3 5l9 8 9-8" fill="none" stroke="var(--blue)" stroke-width="2"/></svg></div>
  sales@puzzlevaultlarkfield.example
</div>
<div class="abs hours">Hours: Wednesday - Fridays (4 to 10pm) Weekends (11am to 9pm)</div>

<div class="abs bottom-bar">
  <span class="abs" style="left:98px;top:18px">© 2019 Copyrights The Company Name.All Rights Reserved</span>
  <div class="abs social" style="left:1054px;top:18px"><span></span><span></span></div>
</div>

</body>
</html>
```